Looking for a cool, modern Cannabis Jar Label

I want you to come up with a better, modern look for a label.

I need it sized to 4” x 3” - I plan to print directly to label printer.

I want you to use Photoshop and deliver me a layered PSD file that I can edit and modify the information as needed..

The label information will need to include places for:
(1) Strain Name - most important part of label - larger font size than rest - example Kestrel Mist, PLV #7, Juniper Hollow
(2) Pricing - for Gram, 1/8, 1/4, 1/2. and Ounce
(3) Strain Designation (Hybrid, Indica or Sativa) - maybe color coded, different color for Indica v. Sativa, just an idea
(4) THC and CBD percentages - for example 23% THC and 0.05% CBD
(5) Farm name - a place where we can add the name/logo of the business that produced the product. example - Ovenrow Farms

I have attached a simple mockup showing the information.

I have also attached a few samples of labels we like to give you an idea of the look and feel we are going for.

I am wanting a very clean, modern, classy, readable look.The font will use is Gotham Font.

HI Everyone! Thank you for all of your designs. I am requesting an extension because I need more time to give adequate feedback to the designers. Thank you for your participation and all of your efforts! I will be making a decision soon!

• Gotham Font

• Thank you for your designs. I am sorry i have been slow in providing feedback, things have been really busy around here!
• I wanted to give some group general feedback. After reviewing all of the designs, there is a common theme among all of the designs that I would like to see changed.
• I would like to see the per gram pricing more prominent on the label. This is what most people are looking for when they are purchasing the product. So I would like to see this stand out from the other pricing tiers. As I think about it, they don't all need to be grouped together in a line. You could have the Per Gram pricing front and center some where and then the other pricing tiers grouped together somewhere else on the label.
• This is the order of importance of items on the label. Items at the the top of the list should be bigger than those below it.
• 1. Strain name
• 2. Pricing - being per gram the most important of all prices
• 3. THC/CBD percentages
• 4. Strain Type (indica, sativa, hybrid)
• 5. Farm name/logo
• When laying out these labels, they will be going on rounded jars and they will be on display. Think of jars with fancy labels in a candy store. They need to be eye catchy, appealing, but easy read.
• Thank you for all of your hard work, everyone is doing a great job.
• Best,
• Neta

```html
<!DOCTYPE html>
<html lang="en">
<head>
<meta charset="UTF-8">
<title>Kestrel Mist Jar Label</title>
<link rel="stylesheet" href="https://fonts.googleapis.com/css2?family=Montserrat:wght@400;600;700;800&family=Oswald:wght@300;400&display=swap">
<style>
  :root {
    --backdrop: #4d4d4d;
    --paper: #ffffff;
    --ink: #111111;
    --accent: #e0245e;
    --accent-deep: #d2145a;
    --muted: #5a5a5a;
    --pill: #555555;
    --logo-box: #888888;
    --leaf-green: #1e8a3c;
    --warn-red: #e31e24;
  }
  * { margin: 0; padding: 0; box-sizing: border-box; }
  html, body { width: 1200px; height: 1200px; overflow: hidden; }
  body { background: var(--backdrop); font-family: "Montserrat", sans-serif; color: var(--ink); position: relative; }

  .jar-label {
    position: absolute; left: 118px; top: 236px; width: 965px; height: 726px;
    background: var(--paper);
  }

  .company-logo {
    position: absolute; left: 29px; top: 34px; width: 203px; height: 204px;
    background: var(--logo-box); color: #fff;
    display: flex; align-items: center; justify-content: center; text-align: center;
    font-size: 32px; line-height: 1.55; font-weight: 400;
  }

  .strain-name {
    position: absolute; left: 257px; top: 18px; width: 691px; height: 235px;
    border: 5px solid var(--accent); border-radius: 28px;
    display: flex; flex-direction: column; align-items: center; justify-content: center;
    font-size: 76px; line-height: 96px; font-weight: 400; letter-spacing: 1px;
    padding-bottom: 6px;
  }

  .strain-type {
    position: absolute; left: 478px; top: 239px; width: 250px; height: 52px;
    background: var(--accent-deep); color: #fff; border-radius: 0 0 8px 8px;
    font-size: 38px; line-height: 52px; text-align: center; letter-spacing: 1px;
  }

  .price-row { position: absolute; left: 0; top: 300px; width: 100%; height: 110px; }
  .price {
    position: absolute; top: 0; width: 190px; margin-left: -95px; text-align: center;
  }
  .price-amount {
    font-family: "Oswald", sans-serif; font-weight: 300; font-size: 68px; line-height: 80px;
    transform: scaleX(0.82); display: inline-block; white-space: nowrap;
  }
  .price-amount sup { font-size: 32px; vertical-align: 30px; margin-left: 2px; }
  .price-unit { font-size: 29px; color: var(--muted); line-height: 32px; margin-top: -4px; }

  .potency-panel {
    position: absolute; left: 18px; top: 427px; width: 351px; height: 281px;
    border: 2.5px solid var(--accent);
  }
  .potency {
    position: absolute; top: 14px; width: 150px; text-align: center;
  }
  .potency-value {
    font-family: "Oswald", sans-serif; font-weight: 300; font-size: 100px; line-height: 110px;
    transform: scaleX(0.82); display: inline-block; white-space: nowrap;
  }
  .potency-value small { font-size: 52px; }
  .potency-label {
    position: absolute; top: 111px; width: 150px; height: 53px;
    background: var(--pill); color: #fff; font-size: 38px; line-height: 53px; text-align: center;
  }
  .potency-thc { left: 0; }
  .potency-thc .potency-label { left: 0; border-radius: 0 10px 10px 0; }
  .potency-cbd { left: 177px; }
  .potency-cbd .potency-label { left: 0; border-radius: 10px 0 0 10px; }
  .activation {
    position: absolute; left: 34px; top: 176px; font-size: 19px; font-weight: 700; white-space: nowrap;
  }
  .potency-divider { position: absolute; left: 8px; right: 8px; top: 206px; border-top: 1.5px solid var(--muted); }
  .lab-info {
    position: absolute; left: 34px; top: 214px; font-size: 15px; font-weight: 700; line-height: 20px;
  }

  .grower-panel {
    position: absolute; left: 368px; top: 427px; width: 402px; height: 281px;
    border-top: 1.5px solid var(--ink); border-bottom: 1.5px solid var(--ink);
    margin-left: 1px; text-align: center;
  }
  .product-kind { font-size: 25px; font-weight: 700; margin-top: 8px; }
  .cultivated-by { font-size: 26px; margin-top: 4px; }
  .grower-mark {
    display: flex; align-items: center; justify-content: center; gap: 18px; margin-top: 26px;
  }
  .grower-mark-square { width: 70px; height: 70px; border-radius: 12px; background: var(--leaf-green); }
  .grower-name { font-size: 38px; font-weight: 800; line-height: 40px; text-align: left; }
  .batch-info { font-size: 16px; font-weight: 700; line-height: 26px; margin-top: 32px; }

  .warning-panel {
    position: absolute; left: 788px; top: 427px; width: 158px; height: 281px;
    border: 2.5px solid var(--ink);
  }
  .warning-text {
    position: absolute; left: 8px; top: 10px; width: 146px;
    font-size: 11.6px; font-weight: 800; line-height: 16.5px; text-transform: uppercase;
  }
  .warning-badge { position: absolute; left: 21px; top: 189px; }
</style>
</head>
<body>
  <main class="jar-label">
    <div class="company-logo">Your<br>Company<br>Logo</div>

    <h1 class="strain-name"><span>Kestrel Mist</span><span>Next line text</span></h1>
    <div class="strain-type">INDICA</div>

    <section class="price-row">
      <div class="price" style="left:98px"><div class="price-amount">€ 10<sup>.00</sup></div><div class="price-unit">Gram</div></div>
      <div class="price" style="left:288px"><div class="price-amount">€ 35<sup>.00</sup></div><div class="price-unit">1/8</div></div>
      <div class="price" style="left:476px"><div class="price-amount">€ 70<sup>.00</sup></div><div class="price-unit">1/4</div></div>
      <div class="price" style="left:668px"><div class="price-amount">€ 140<sup>.00</sup></div><div class="price-unit">1/2</div></div>
      <div class="price" style="left:857px"><div class="price-amount">€ 280<sup>.00</sup></div><div class="price-unit">Ounce</div></div>
    </section>

    <section class="potency-panel">
      <div class="potency potency-thc">
        <div class="potency-value">23<small>%</small></div>
        <div class="potency-label">THC</div>
      </div>
      <div class="potency potency-cbd">
        <div class="potency-value">0.5<small>%</small></div>
        <div class="potency-label">CBD</div>
      </div>
      <div class="activation">Activation time:&nbsp; Immediately</div>
      <div class="potency-divider"></div>
      <div class="lab-info">Tested by: Lorem Ipsum<br>No. ref: 1234567890123456<br>Test Date:</div>
    </section>

    <section class="grower-panel">
      <div class="product-kind">Cannabis Flower</div>
      <div class="cultivated-by">Cultivated By:</div>
      <div class="grower-mark">
        <div class="grower-mark-square"></div>
        <div class="grower-name">TALLGRASS<br>GROW</div>
      </div>
      <div class="batch-info">Harvest Date:<br>Batch No. 1234567890123456</div>
    </section>

    <section class="warning-panel">
      <p class="warning-text">Keep out of reach of children and animals. Cannabis products may only be possessed or consumed by persons 21 years of age or older unless the person is a qualified patient.</p>
      <svg class="warning-badge" width="103" height="82" viewBox="0 0 103 82" aria-hidden="true">
        <rect x="2" y="2" width="99" height="78" rx="8" fill="#ffffff" stroke="var(--ink)" stroke-width="4"/>
        <rect x="36" y="6" width="61" height="70" rx="4" fill="var(--warn-red)"/>
      </svg>
    </section>
  </main>
</body>
</html>
```